Veldmark Supplies Business Card

Professional business card that stand out to our potential customers. Front and back with clean modern design

Industry/Entity Type

Oil and gas

Contact Information for Business Card

Name, address, website , office phone and cell number

Requirements
Must have
• Editable files for each employee

```html
<!DOCTYPE html>
<html lang="en">
<head>
<meta charset="utf-8">
<title>Veldmark Supplies Business Card</title>
<link rel="stylesheet" href="https://fonts.googleapis.com/css2?family=Poppins:wght@400;500;700&display=swap">
<style>
  :root {
    --bg: #dcdcdc;
    --card-white: #f7f7f7;
    --card-black: #0e0e0e;
    --accent-red: #f20d12;
    --paper-ink: #1d1d1d;
    --reverse-ink: #ffffff;
    --rule: #8a8a8a;
  }
  * { box-sizing: border-box; margin: 0; padding: 0; }
  html, body {
    width: 1200px; height: 930px; overflow: hidden;
    background: var(--bg);
    font-family: "Poppins", sans-serif;
  }
  .canvas { position: relative; width: 1200px; height: 930px; }
  .card {
    position: absolute;
    width: 600px; height: 343px;
    box-shadow: 0 10px 30px rgba(0,0,0,0.12);
  }
  .card-back {
    left: 520px; top: 130px;
    background: var(--card-black);
    display: flex; align-items: center; justify-content: center;
  }
  .card-front {
    left: 80px; top: 460px;
    background: var(--card-white);
    display: flex; flex-direction: column; align-items: center;
    padding-top: 58px;
  }
  .wordmark {
    font-weight: 700; text-transform: uppercase; letter-spacing: 0.06em;
    white-space: nowrap;
  }
  .card-back .wordmark { font-size: 32px; color: var(--reverse-ink); }
  .card-front .wordmark { font-size: 24px; color: var(--paper-ink); }
  .holder-name {
    margin-top: 26px;
    color: var(--accent-red);
    font-weight: 700; font-size: 17px; letter-spacing: 0.08em; text-transform: uppercase;
  }
  .contact {
    margin-top: 20px;
    display: flex; align-items: stretch; gap: 16px;
    font-size: 13.5px; color: var(--paper-ink); line-height: 1.55;
  }
  .contact-address { text-align: right; font-style: normal; }
  .contact-rule { width: 1px; background: var(--rule); }
  .contact-list { list-style: none; }
  .contact-list li { display: flex; align-items: center; gap: 8px; white-space: nowrap; }
  .contact-list svg { width: 13px; height: 13px; flex: none; }
</style>
</head>
<body>
<main class="canvas">
  <section class="card card-back" aria-label="Card back">
    <div class="wordmark">Veldmark Supplies</div>
  </section>

  <section class="card card-front" aria-label="Card front">
    <div class="wordmark">Veldmark Supplies</div>
    <h1 class="holder-name">Daniel Harlow</h1>
    <div class="contact">
      <address class="contact-address">
        421, Address line<br>goes here<br>45452, Country Name
      </address>
      <span class="contact-rule"></span>
      <ul class="contact-list">
        <li>
          <svg viewBox="0 0 16 16" aria-hidden="true"><path d="M4 1.5l2.2 3-1.4 1.6c.9 2 2.3 3.4 4.3 4.3l1.6-1.4 3 2.2-1.2 2.6C7.2 13.6 2.4 8.8 1.4 2.7z" fill="none" stroke="#f20d12" stroke-width="1.5" stroke-linejoin="round"/></svg>
          044-555 010 234
        </li>
        <li>
          <svg viewBox="0 0 16 16" aria-hidden="true"><rect x="4" y="1" width="8" height="14" rx="1.5" fill="none" stroke="#f20d12" stroke-width="1.5"/><circle cx="8" cy="12.3" r="0.9" fill="#f20d12"/></svg>
          044-555 010 234
        </li>
        <li>
          <svg viewBox="0 0 16 16" aria-hidden="true"><circle cx="8" cy="8" r="6.5" fill="none" stroke="#f20d12" stroke-width="1.4"/><ellipse cx="8" cy="8" rx="2.8" ry="6.5" fill="none" stroke="#f20d12" stroke-width="1.2"/><path d="M1.5 8h13M2.6 4.6h10.8M2.6 11.4h10.8" stroke="#f20d12" stroke-width="1.1"/></svg>
          www.veldmarksupplies.com
        </li>
      </ul>
    </div>
  </section>
</main>
</body>
</html>
```